Wordpress 6 pages GLAM design for hair salon

Hi guys.
I need a glam & easy to navigate web design for my (women only) new hair salon.
I have a logo. You can see in attached files.
I like 3d backgrounds.
My favourite colours choice: any variety of pink(hot & very soft), white, black, grey.
I would like to see website very feminine, glamorous & kind of old Hollywood and Dorinda Calloway inspired.
Of course it should have plug ins, like social media, map, security etc.
My website now: http://velmoracoiffure.example

Designs what I like:
http://torvinellastudio.example
http://pelurabeautyloft.example
http://www.quillfernvisualworks.example/boutique-graphic-web-folio.html
Updates

Target Market(s)

WOMEN

Industry/Entity Type

Boutique

Requirements
Should not have
• any cartoon or other characters!

```html
<!DOCTYPE html>
<html lang="en">
<head>
<meta charset="utf-8">
<title>Velmora Metro Coiffure</title>
<link href="https://fonts.googleapis.com/css2?family=Gabriela&family=Open+Sans:wght@400;600;700&display=swap" rel="stylesheet">
<style>
:root{
  --ink:#1a1a1a;
  --night:#050505;
  --leather-a:#2a2422;
  --leather-b:#0d0b0a;
  --blush:#fbdde9;
  --rose:#d4558a;
  --rose-deep:#b83c70;
  --rose-edge:#e48ab0;
  --wine:#8a1544;
  --rule:#d9b5c4;
  --white:#ffffff;
}
*{margin:0;padding:0;box-sizing:border-box}
html,body{width:975px;height:1200px;overflow:hidden}
body{
  position:relative;
  background:radial-gradient(ellipse at 50% 45%,var(--leather-a) 0%,var(--leather-b) 75%);
  font-family:"Open Sans",sans-serif;color:var(--ink);
}
.top-shade{position:absolute;left:0;top:0;width:975px;height:120px;background:linear-gradient(var(--night),rgba(5,5,5,0))}
.brand{position:absolute;left:0;top:60px;width:975px;text-align:center;font-family:"Gabriela",serif;font-size:28px;color:var(--white);letter-spacing:1px}
.bar{position:absolute;left:123px;width:727px;height:6px;background:var(--rose)}
.bar.top{top:149px}.bar.bottom{top:1128px}
.panel{position:absolute;left:152px;top:155px;width:672px;height:973px;background:var(--blush);
  border-left:14px solid var(--rose-edge);border-right:14px solid var(--rose-edge)}
.abs{position:absolute}
.nav{left:183px;top:180px;width:607px;height:34px;border-bottom:1px solid var(--rule)}
.nav a{position:absolute;top:2px;font-family:"Gabriela",serif;font-size:15px;color:var(--wine);text-decoration:none}
.rule{height:1px;background:var(--rule)}
.photo{border:3px solid var(--white)}
h1,h2{font-family:"Gabriela",serif;font-weight:400}
h1{font-size:22px;color:var(--ink)}
h2{font-size:21px;color:var(--wine)}
p{white-space:nowrap}
.welcome p{font-size:10.8px;line-height:19px;margin-bottom:7px}
.services p{font-size:9.7px;line-height:18px;margin-bottom:9px}
.cta{left:350px;top:398px;width:381px;height:53px;background:linear-gradient(var(--rose-edge),var(--rose-deep));
  border-top:4px solid var(--rose-edge);color:var(--white)}
.cta .label{position:absolute;left:34px;top:11px;font-size:11.5px;font-weight:600;line-height:15px;letter-spacing:.3px}
.cta .phone{position:absolute;left:218px;top:11px;font-size:17px;font-weight:700}
.contact{font-size:11.5px;line-height:26px;white-space:nowrap}
.copyright{left:0;top:1158px;width:975px;text-align:center;font-size:10px;color:var(--white)}
</style>
</head>
<body>
<div class="top-shade"></div>
<div class="brand">Velmora Metro Coiffure</div>
<div class="bar top"></div>
<div class="panel"></div>
<div class="bar bottom"></div>

<nav class="abs nav">
  <a style="left:93px">Home</a>
  <a style="left:158px">About Us</a>
  <a style="left:243px">Services</a>
  <a style="left:318px">Gallery</a>
  <a style="left:387px">Blog</a>
  <a style="left:440px">Contact Us</a>
</nav>

<div class="abs photo" style="left:192px;top:259px;width:132px;height:150px;background:linear-gradient(150deg,#6b5a5e,#c9b4b6 60%,#9e8f8c)" role="img" aria-label="Salon interior with styling chairs and product shelves"></div>
<section class="abs welcome" style="left:349px;top:257px;width:450px">
  <h1 style="margin-bottom:9px">Welcome to our site</h1>
  <p>Our salon is based on the belief that our customers' needs are of the utmost importance.<br>Our team is committed to meeting those needs. As a result, a high percentage of our<br>business is from repeat customers and referrals.</p>
  <p>We would welcome the opportunity to earn your trust and deliver you the best service<br>in the industry!</p>
</section>
<div class="abs cta">
  <div class="label">CALL TODAY TO BOOK YOUR<br>APPOINTMENT</div>
  <div class="phone">555-014-2290</div>
</div>

<div class="abs rule" style="left:186px;top:478px;width:606px"></div>

<section class="abs services" style="left:193px;top:500px;width:280px">
  <h2 style="margin-bottom:10px">Our Services</h2>
  <p>Continuously upgrading skills in order to perfect the latest<br>looks by incorporating the hottest trends and styles with<br>traditional elements, providing you a myriad of options<br>that combine fresh, chic and classic lines.</p>
  <p>I will assist you with any questions you may have. Whether<br>it be totally new look or just a trim – we can work together<br>to achieve the look that suits you best.</p>
</section>
<div class="abs" style="left:194px;top:682px;width:98px;height:107px;background:linear-gradient(135deg,#1b1a19,#8a7a66)" role="img" aria-label="Long sleek blonde hairstyle"></div>
<div class="abs" style="left:296px;top:682px;width:95px;height:107px;background:linear-gradient(135deg,#f2f0ef,#4a3b38)" role="img" aria-label="Dark layered hairstyle with fringe"></div>
<div class="abs" style="left:192px;top:791px;width:96px;height:107px;background:linear-gradient(135deg,#2a2020,#4d3935)" role="img" aria-label="Long dark wavy hairstyle"></div>
<div class="abs" style="left:292px;top:791px;width:99px;height:107px;background:linear-gradient(135deg,#ece9e6,#7a5b48)" role="img" aria-label="Soft brown feathered hairstyle"></div>

<section class="abs" style="left:502px;top:500px">
  <h2>Gallery</h2>
</section>
<div class="abs" style="left:506px;top:540px;width:136px;height:105px;background:linear-gradient(135deg,#c9cfd2,#d8c8a4)" role="img" aria-label="Crimped platinum hairstyle"></div>
<div class="abs" style="left:650px;top:540px;width:136px;height:105px;background:linear-gradient(135deg,#b8c0c2,#e3d6bf)" role="img" aria-label="Blonde updo hairstyle"></div>
<div class="abs" style="left:506px;top:655px;width:136px;height:105px;background:linear-gradient(135deg,#1d1b1a,#c98a55)" role="img" aria-label="Copper curly hairstyle"></div>
<div class="abs" style="left:650px;top:655px;width:136px;height:105px;background:linear-gradient(135deg,#262322,#5a3a2c)" role="img" aria-label="Voluminous brunette updo"></div>
<div class="abs" style="left:506px;top:773px;width:136px;height:105px;background:linear-gradient(135deg,#3a2a2a,#1a1212)" role="img" aria-label="Glossy dark side-swept hairstyle"></div>
<div class="abs" style="left:650px;top:773px;width:136px;height:105px;background:linear-gradient(135deg,#8e978f,#b8643a)" role="img" aria-label="Red vintage pinned updo"></div>

<div class="abs rule" style="left:186px;top:930px;width:606px"></div>

<section class="abs" style="left:188px;top:946px">
  <h2>Location</h2>
</section>
<div class="abs contact" style="left:274px;top:1004px">
  <div>Telephone:+1 555 014 2290</div>
  <div>hello@velmoracoiffure.example</div>
</div>
<div class="abs" style="left:486px;top:950px;width:300px;height:152px;border:2px solid var(--white);background:linear-gradient(135deg,#e6e2da,#d9d4c8)" role="img" aria-label="Street map showing the salon location"></div>

<div class="abs copyright">Copyrights @ 2014 All Rights Reserved</div>
</body>
</html>
```